Family history tech product tailored for moms needs banner ads

loomi.com is launching next week and we've partnered with an ad group that will be launching a campaign on school district websites that will be pushed to 250k moms of school age children.

We're launching a $199 product that shows you more about who you are through your family's history. We connect people wanting to learn more about themselves with expert researcher/genealogist who will uncover their past and find the stories of their ancestors.

See branding guidelines below as well as the landing page we're designing where these ads will take you.

Here is the landing page design:
https://files.quellbox-share.com/Q93KD8R71-P2ZXW4KL8-ab12cd34ef

Target Market(s)

Mom's of kids in elementary and middle school.

Persona:
Mom, 38 years old, 2 kids (age 6 and 8)
Lives in Dallas, drives a 2016 Norvik Stallard
She and husband met in college. She was a nurse, but she stopped working to be a full-time mom
Husband is in financial consulting, household income of $140,000
When kids at school, she runs errands, works out, meets up with girlfriends for coffee
She shops at Fernabelle, has active hobbies
She is always busy, there’s not enough time for her family; she is worried that her kids may become distant because of how busy the family is
She values time with family most, soccer weekends, financial stability, college for the kids
Wants to connect more with the kids and the family to increase the bond, and she thinking having more context for the family will help them bond around a common history
Her objections to Loomi are lack of trust in a new service, time it will cost her to get the info she wants to achieve her goals

Industry/Entity Type

Startup

Other font styles liked:
• follow style guide

Requirements
Must have
• Must follow the design pattern in our branding guide.
• https://www.stashpail.com/s/qk7m2x9vbn4wtr8/Capture%202016-11-30%2013.39.48.png?dl=0
Nice to have
• Good copy, I'm less worried about that though. We can work together on that.
Should not have
• Stock imagery that sucks. I'm really opposed to anything that looks like it is from the 2001 - 2011

```html
<!DOCTYPE html>
<html lang="en">
<head>
<meta charset="utf-8">
<title>Loomi banner – Find yours</title>
<link rel="stylesheet" href="https://fonts.googleapis.com/css2?family=Open+Sans:wght@400;600;700&display=swap">
<style>
  :root {
    --ink: #3d4f66;
    --teal: #1798a5;
    --cyan: #45cbd6;
    --brand-blue: #2f8ef0;
    --pale-blue: #cfe4fb;
    --shadow: #d5d5d5;
    --white: #ffffff;
  }
  * { margin: 0; padding: 0; box-sizing: border-box; }
  html, body { width: 1200px; height: 148px; overflow: hidden; background: var(--white); }
  .banner {
    position: relative;
    width: 1200px;
    height: 148px;
    overflow: hidden;
    background: var(--white);
    font-family: "Open Sans", Arial, sans-serif;
  }
  .texture {
    position: absolute;
    left: 0; top: 0;
    width: 420px; height: 148px;
    background: linear-gradient(100deg, rgba(207,228,251,0.55) 0%, rgba(207,228,251,0.25) 55%, rgba(255,255,255,0) 100%);
  }
  .headline {
    position: absolute;
    left: 33px; top: 30px;
    color: var(--ink);
    font-weight: 700;
    font-size: 25px;
    line-height: 35px;
    letter-spacing: -0.2px;
  }
  .headline span { display: block; }
  .headline .second { padding-left: 37px; }
  .cta {
    position: absolute;
    left: 423px; top: 63px;
    width: 240px; height: 57px;
    background: var(--teal);
    color: var(--white);
    font-weight: 700;
    font-size: 33px;
    display: flex; align-items: center; justify-content: center;
    text-decoration: none;
    box-shadow: 10px 10px 0 var(--shadow);
  }
  .hands {
    position: absolute;
    left: 738px; top: 0;
    width: 150px; height: 148px;
    background: radial-gradient(ellipse 45% 70% at 52% 55%, #f1cdb8 0%, #e9c1aa 45%, rgba(207,228,251,0.9) 75%, rgba(207,228,251,0) 100%);
  }
  .brand {
    position: absolute;
    left: 968px; top: 14px;
    display: flex; align-items: center; gap: 8px;
    color: var(--brand-blue);
    font-weight: 700;
    font-size: 28px;
    line-height: 36px;
  }
  .brand-dot {
    width: 26px; height: 26px;
    border-radius: 50%;
    background: var(--brand-blue);
  }
  .tagline {
    position: absolute;
    left: 968px; top: 74px;
    width: 227px; height: 47px;
    background: var(--cyan);
    color: var(--white);
    font-size: 14px;
    letter-spacing: 1.6px;
    display: flex; align-items: center; justify-content: center;
    box-shadow: 8px 8px 0 var(--shadow);
  }
</style>
</head>
<body>
  <div class="banner">
    <div class="texture" role="img" aria-label="Soft pale blue diagonal stripe texture"></div>
    <h1 class="headline">
      <span class="first">Everyone has a story…</span>
      <span class="second">A unique family story ...</span>
    </h1>
    <a class="cta" href="#">Find yours</a>
    <div class="hands" role="img" aria-label="Photo of an adult hand and a child's hand pressed palm to palm over pale blue stripes"></div>
    <div class="brand">
      <span class="brand-dot"></span>
      <span class="brand-name">Loomi</span>
    </div>
    <div class="tagline">Yourself, Discovered.</div>
  </div>
</body>
</html>
```